Zvo Klinieken website for a maxillofacial surgery clinic

It's a website for a clinic for maxillofacial surgery in WordPress . The website doesn't need to be complicated but has to look professional. It needs to be in Dutch so i can give the texts. Similar websites are www.tandartsenpraktijkveldorm.nl or www.pbtspecialisten.nl. Pages would be sort of similar to https://hetcentrumvoorgezichtszorg.nl/ or https://wervelmondclinics.nl/. Those lasts are maxillofacial surgery clinic websites, but there are little more extensive.
I uploaded the logo. If this is not the proper quality i can upload the eps. Logo was made through pixelforum.

Target Market(s)

Patients who can find me and see information about the clinic

Industry/Entity Type

Healthcare

Coding

Coded - Design and coding required

Number of Pages Required

5+ page

Font styles to use
Other font styles liked:
• Something standard professional

Colors
0054AA
0677BA
7BADD7
CADEEF
E8F1F8

Requirements
Nice to have
• Something in line with the logo. I prefer a little dark like the darker logos but I'm not sure if that's professional. Logos bkvzo and rlpw are instances i'm registered to so they will have to be on the website too but small somewhere.

```html
<!DOCTYPE html>
<html lang="nl">
<head>
<meta charset="utf-8">
<title>Zvo Klinieken</title>
<link href="https://fonts.googleapis.com/css2?family=Montserrat:wght@400;500;600;700&display=swap" rel="stylesheet">
<style>
:root{
  --blue:#3aaee3;
  --slate:#6a7ea6;
  --ink:#111;
  --text:#555;
  --pale:#e6f3fb;
  --grey:#f4f4f4;
  --dark:#47484b;
  --black:#000;
}
*{box-sizing:border-box;margin:0;padding:0}
html,body{width:1200px;height:3717px;overflow:hidden;background:#fff;font-family:'Montserrat',sans-serif;color:var(--ink)}
.canvas{position:relative;width:1200px;height:3717px;overflow:hidden}
.abs{position:absolute}
.btn{position:absolute;display:flex;align-items:center;justify-content:center;gap:8px;background:var(--slate);color:#fff;border-radius:5px;font-weight:600;font-size:16px;letter-spacing:.3px}
.btn .dot{width:13px;height:13px;border-radius:50%;background:#fff;position:relative}
.btn .dot::after{content:"";position:absolute;left:4px;top:3.5px;border-left:5px solid var(--slate);border-top:3px solid transparent;border-bottom:3px solid transparent}
.brand{display:flex;align-items:center;gap:8px;font-weight:700;color:var(--blue)}
.brand .mark{border-radius:50%;background:var(--blue)}
.nav a{position:absolute;top:38px;font-size:18px;color:#333;text-decoration:none}
.section-title{position:absolute;font-size:36px;font-weight:700;color:var(--ink)}
.section-title span{color:var(--blue)}
.rule{position:absolute;height:3px;background:var(--blue)}
.para{position:absolute;font-size:16px;line-height:25.8px;color:var(--text);text-align:justify}
.photo{position:absolute}
.card{position:absolute;background:#fff;border-radius:14px;box-shadow:0 3px 10px rgba(0,0,0,.15);text-align:center}
.card .icon{width:112px;height:112px;border-radius:50%;margin:16px auto 0;background:var(--slate)}
.card h3{font-size:21px;font-weight:600;margin-top:22px}
.card .mini{width:42px;height:3px;background:var(--slate);margin:10px auto 0}
.card p{font-size:15px;line-height:26px;color:var(--text);padding:12px 9px 0;text-align:justify}
.arrow{position:absolute;width:38px;height:38px;border-radius:50%;display:flex;align-items:center;justify-content:center}
.blog{position:absolute;background:#fff;box-shadow:0 2px 8px rgba(0,0,0,.12);text-align:center}
.blog .img{height:179px}
.blog .date{position:absolute;left:69px;top:168px;width:176px;height:31px;background:var(--blue);color:#fff;font-size:16px;line-height:31px}
.blog h3{font-size:21px;font-weight:500;margin-top:44px}
.blog p{font-size:15px;line-height:26px;color:var(--text);padding:8px 26px 0;text-align:justify}
.info .circle{position:absolute;width:70px;height:70px;border-radius:50%;background:#fff;box-shadow:0 2px 8px rgba(0,0,0,.15);display:flex;align-items:center;justify-content:center}
.info h4{position:absolute;font-size:19px;font-weight:700;color:var(--blue)}
.info p{position:absolute;font-size:16px;line-height:25px;color:#333}
.field{position:absolute;background:#fff;border:1px solid #eee;border-radius:3px;box-shadow:0 2px 7px rgba(0,0,0,.13);font-size:16px;color:#333;padding:0 22px;display:flex;align-items:center;justify-content:space-between}
.footer-links a{position:absolute;top:3592px;font-size:18px;font-weight:700;color:#fff;text-decoration:none}
.social{position:absolute;top:3646px;width:40px;height:40px;border-radius:50%;border:2px solid var(--blue)}
</style>
</head>
<body>
<div class="canvas">

<!-- Header -->
<header>
  <div class="brand abs" style="left:123px;top:30px;font-size:26px"><span class="mark" style="width:26px;height:26px"></span>Zvo Klinieken</div>
  <nav class="nav">
    <a style="left:457px">Home</a>
    <a style="left:542px">Over</a>
    <a style="left:614px">Diensten &#8964;</a>
    <a style="left:741px">Bloggen</a>
    <a style="left:847px">Contact</a>
  </nav>
  <div class="btn" style="left:946px;top:29px;width:142px;height:39px">BEGIN <span class="dot"></span></div>
</header>

<!-- Hero -->
<section class="hero">
  <div class="photo" role="img" aria-label="Moderne tandheelkundige behandelkamer met gang" style="left:0;top:98px;width:1200px;height:560px;background:linear-gradient(90deg,#35373a 0%,#5a5d60 35%,#b9b3a4 65%,#d9c26a 85%,#9a9a8e 100%)"></div>
  <svg class="abs" style="left:0;top:500px" width="1200" height="160" viewBox="0 0 1200 160">
    <polygon points="0,135 865,12 1200,150 1200,160 0,160" fill="#3aaee3"/>
    <polygon points="0,156 865,40 1200,160 0,160" fill="#fff"/>
  </svg>
  <div class="abs" style="left:111px;top:252px;font-size:37px;color:#fff">Welcome To</div>
  <div class="abs" style="left:109px;top:292px;font-size:52px;font-weight:700;color:var(--blue)">Zvo klinieken</div>
  <div class="abs" style="left:111px;top:355px;width:416px;font-size:18.5px;line-height:26px;color:#fff;text-align:justify;text-align-last:justify">Lorem ipsum dolor sit amet, consectetur adipiscing elit, sed do eiusmod tempor</div>
  <div class="btn" style="left:111px;top:436px;width:143px;height:39px">BEGIN <span class="dot"></span></div>
</section>

<!-- About -->
<section class="about">
  <h2 class="section-title" style="left:111px;top:733px">OVER <span>Zvo Klinieken</span></h2>
  <div class="rule" style="left:111px;top:785px;width:87px"></div>
  <p class="para" style="left:111px;top:811px;width:489px">Lorem ipsum dolor sit amet, consectetur adipiscing elit, sed do eiusmod tempor incididunt ut labore et dolore magna aliqua. Quis ipsum suspendisse ultrices gravida. Risus commodo viverra maecenas accumsan lacus vel facilisis. Lorem ipsum dolor sit amet, consectetur adipiscing elit, sed do eiusmod tempor incididunt ut labore et dolore magna aliqua. Quis ipsum suspendisse ultrices gravida. Risus commodo viverra maecenas accumsan lacus vel facilisis.</p>
  <div class="btn" style="left:111px;top:1040px;width:143px;height:39px">Leren Meer <span class="dot"></span></div>
  <svg class="abs" style="left:630px;top:790px" width="470" height="320" viewBox="0 0 470 320">
    <polyline points="265,308 12,308 12,72 30,72" fill="none" stroke="#3aaee3" stroke-width="4"/>
    <path d="M424,20 A88,110 0 0 1 424,218" fill="none" stroke="#3aaee3" stroke-width="14"/>
  </svg>
  <div class="photo" role="img" aria-label="Scherm met digitale gebitsscan in behandelkamer" style="left:663px;top:744px;width:391px;height:328px;background:linear-gradient(135deg,#8d9296,#dfe2e4 45%,#c7cbcd)"></div>
</section>

<!-- What we do -->
<section class="work">
  <div class="abs" style="left:0;top:1270px;width:1200px;height:473px;background:var(--grey)"></div>
  <div class="photo" role="img" aria-label="Donkere close-up van een patiënt bij behandeling" style="left:0;top:1186px;width:541px;height:557px;background:linear-gradient(160deg,#5d5e61,#3c3d40);clip-path:polygon(0 0,310px 0,541px 100%,0 100%)"></div>
  <div class="abs" style="left:195px;top:1356px;width:456px;height:303px;background:var(--blue)"></div>
  <div class="photo" role="img" aria-label="Behandelkamer met tandartsstoel en houten wand" style="left:180px;top:1338px;width:453px;height:299px;background:linear-gradient(120deg,#d8d6d2,#a69786 50%,#5e5a57)"></div>
  <h2 class="section-title" style="left:700px;top:1328px">Wat <span>We Doen</span></h2>
  <div class="rule" style="left:700px;top:1381px;width:87px"></div>
  <p class="para" style="left:700px;top:1406px;width:389px;height:155px;overflow:hidden">Lorem ipsum dolor sit amet, consectetur adipiscing elit, sed do eiusmod tempor incididunt ut labore et dolore magna aliqua. Quis ipsum suspendisse ultrices gravida. Risus commodo viverra maecenas accumsan lacus vel facilisis. Lorem ipsum dolor sit amet, consectetur adipiscing elit.</p>
  <div class="btn" style="left:695px;top:1581px;width:142px;height:39px">Leren Meer <span class="dot"></span></div>
</section>

<!-- Services -->
<section class="services">
  <h2 class="section-title" style="left:0;width:1200px;text-align:center;top:1822px">Ons <span>Diensten</span></h2>
  <div class="rule" style="left:560px;top:1876px;width:83px"></div>
  <div class="arrow" style="left:111px;top:2046px;background:#7b7b7b">
    <svg width="14" height="14" viewBox="0 0 14 14"><polyline points="9,2 4,7 9,12" fill="none" stroke="#fff" stroke-width="2"/></svg></div>
  <div class="arrow" style="left:1051px;top:2046px;background:var(--blue)">
    <svg width="14" height="14" viewBox="0 0 14 14"><polyline points="5,2 10,7 5,12" fill="none" stroke="#fff" stroke-width="2"/></svg></div>
  <div class="card" style="left:193px;top:1924px;width:232px;height:283px">
    <div class="icon"></div><h3>Lorem ipsum dolor</h3><div class="mini"></div>
    <p>Lorem ipsum dolor sit amet, consectetur adipiscing elit, sed do eiusmod tempor</p></div>
  <div class="card" style="left:486px;top:1924px;width:231px;height:283px;box-shadow:0 6px 18px rgba(0,0,0,.25)">
    <div class="icon" style="background:#9fdcf6"></div><h3>Lorem ipsum dolor</h3><div class="mini"></div>
    <p>Lorem ipsum dolor sit amet, consectetur adipiscing elit, sed do eiusmod tempor</p></div>
  <div class="card" style="left:785px;top:1924px;width:232px;height:283px">
    <div class="icon"></div><h3>Lorem ipsum dolor</h3><div class="mini"></div>
    <p>Lorem ipsum dolor sit amet, consectetur adipiscing elit, sed do eiusmod tempor</p></div>
</section>

<!-- Blog -->
<section class="blogs">
  <div class="abs" style="left:0;top:2293px;width:1200px;height:610px;background:var(--pale)"></div>
  <h2 class="section-title" style="left:0;width:1200px;text-align:center;top:2373px">Laatste <span>Bloggen</span></h2>
  <div class="rule" style="left:557px;top:2427px;width:86px"></div>
  <article class="blog" style="left:111px;top:2472px;width:314px;height:345px">
    <div class="img" role="img" aria-label="Röntgenfoto van een gebit op een tablet" style="background:linear-gradient(135deg,#c8d4e2,#7d8a9a)"></div>
    <div class="date">Dec 09,2023</div><h3>Lorem ipsum dolor</h3>
    <p>Lorem ipsum dolor sit amet, consectetur adipiscing elit, sed do eiusmod tempor incididunt ut</p></article>
  <article class="blog" style="left:443px;top:2472px;width:314px;height:345px">
    <div class="img" role="img" aria-label="Chirurgisch team aan het werk" style="background:linear-gradient(135deg,#3d5f8c,#b9cfe0)"></div>
    <div class="date">Dec 09,2023</div><h3>Lorem ipsum dolor</h3>
    <p>Lorem ipsum dolor sit amet, consectetur adipiscing elit, sed do eiusmod tempor incididunt ut</p></article>
  <article class="blog" style="left:775px;top:2472px;width:314px;height:345px">
    <div class="img" role="img" aria-label="Tandarts behandelt een kind in de stoel" style="background:linear-gradient(135deg,#3e9ea3,#d7e4ea)"></div>
    <div class="date">Dec 09,2023</div><h3>Lorem ipsum dolor</h3>
    <p>Lorem ipsum dolor sit amet, consectetur adipiscing elit, sed do eiusmod tempor incididunt ut</p></article>
</section>

<!-- Contact -->
<section class="contact">
  <h2 class="section-title" style="left:0;width:1200px;text-align:center;top:2980px">Contact <span>Ons</span></h2>
  <div class="rule" style="left:557px;top:3034px;width:86px"></div>
  <div class="info">
    <div class="circle" style="left:109px;top:3067px"><svg width="24" height="30" viewBox="0 0 24 30"><path d="M12 0C5 0 0 5 0 12c0 8 12 18 12 18s12-10 12-18C24 5 19 0 12 0z" fill="#3aaee3"/><circle cx="12" cy="11" r="4.5" fill="#fff"/></svg></div>
    <h4 style="left:196px;top:3072px">Plaats</h4>
    <p style="left:198px;top:3098px;width:160px">Lorem ipsum dolor sit amet,</p>
    <div class="circle" style="left:109px;top:3165px"><svg width="30" height="22" viewBox="0 0 30 22"><rect width="30" height="22" rx="2" fill="#3aaee3"/><polyline points="1,2 15,12 29,2" fill="none" stroke="#fff" stroke-width="2"/></svg></div>
    <h4 style="left:196px;top:3171px">E-mail Ons</h4>
    <p style="left:198px;top:3198px">info@zvoklinieken.nl</p>
    <div class="circle" style="left:109px;top:3248px"><svg width="28" height="28" viewBox="0 0 28 28"><path d="M6 1l5 6-3 4c2 4 5 7 9 9l4-3 6 5-3 5C12 27 1 16 1 5z" fill="#3aaee3"/></svg></div>
    <h4 style="left:196px;top:3256px">Telefoon</h4>
    <p style="left:198px;top:3283px">+31 20 555 0188</p>
  </div>
  <div class="field" style="left:410px;top:3076px;width:321px;height:50px">Jouw Naam <span style="width:13px;height:13px;border-radius:50%;background:#333"></span></div>
  <div class="field" style="left:410px;top:3141px;width:321px;height:48px">E-mail Adres <span style="width:15px;height:11px;background:#333;border-radius:1px"></span></div>
  <div class="field" style="left:410px;top:3205px;width:321px;height:47px">Telefoon <svg width="14" height="14" viewBox="0 0 28 28"><path d="M6 1l5 6-3 4c2 4 5 7 9 9l4-3 6 5-3 5C12 27 1 16 1 5z" fill="#333"/></svg></div>
  <div class="field" style="left:410px;top:3270px;width:321px;height:47px">Adres <svg width="11" height="14" viewBox="0 0 24 30"><path d="M12 0C5 0 0 5 0 12c0 8 12 18 12 18s12-10 12-18C24 5 19 0 12 0z" fill="#333"/></svg></div>
  <div class="field" style="left:766px;top:3076px;width:323px;height:178px;align-items:flex-start;padding-top:14px">Bericht <span style="width:18px;height:13px;border-radius:50%;background:#333"></span></div>
  <div class="btn" style="left:766px;top:3278px;width:143px;height:39px">INDIENEN <span class="dot"></span></div>
</section>

<!-- Footer -->
<footer>
  <svg class="abs" style="left:0;top:3370px" width="1200" height="347" viewBox="0 0 1200 347">
    <polygon points="0,2 865,127 1200,12 1200,347 0,347" fill="#3aaee3"/>
    <polygon points="0,26 865,152 1200,37 1200,347 0,347" fill="#000"/>
  </svg>
  <div class="brand abs" style="left:111px;top:3620px;font-size:27px"><span class="mark" style="width:26px;height:26px"></span>Zvo Klinieken</div>
  <nav class="footer-links">
    <a style="left:404px">Home</a>
    <a style="left:490px">Over</a>
    <a style="left:565px">Diensten</a>
    <a style="left:684px">Bloggen</a>
    <a style="left:792px">Contact</a>
  </nav>
  <div class="abs" style="left:404px;top:3630px;width:685px;height:1px;background:#555"></div>
  <div class="social" style="left:404px" aria-label="Sociaal netwerk"></div>
  <div class="social" style="left:456px" aria-label="Sociaal netwerk"></div>
  <div class="social" style="left:508px" aria-label="Sociaal netwerk"></div>
  <div class="abs" style="right:111px;top:3656px;font-size:16px;color:#fff">&copy; 2023 Zvo Klinieken. Alle Rechten Gereserveerd.</div>
</footer>

</div>
</body>
</html>
```